Horseracing 8 page brochure - tight turnaround, deadline tomorrow 12GMT

Hi - we have a brochure already drafted for our annual open day at our horseracing stables in England, but it needs a professional design please! The design should convey that this is a smart, professional yard. We brand in a dark blue (as seen on the logo on the back page) and shades of blue. We have a range of other landscape / action photos available. This needs an almost instant turnaround please

Target Market(s)

Racehorse owners - current and prospective. High net worth / socio economic group

Industry/Entity Type

It Professional

Other font styles liked:
• As per 'Rhys Dalby' text

Colors
0255a3
3176b5
85abd2
cedeed

Requirements
Must have
• All text and images in publisher file provided below. Other photos are optional for space filling / backrounds

```html
<!DOCTYPE html>
<html lang="en">
<head>
<meta charset="utf-8">
<title>Chalkdown Racing – Annual Open Day Brochure</title>
<link href="https://fonts.googleapis.com/css2?family=Arimo:wght@400&family=Arvo:wght@400;700&family=Crimson+Text:wght@400&display=swap" rel="stylesheet">
<style>
  :root{
    --navy:#2b1f6e;
    --navy-deep:#2a1d68;
    --navy-band-end:#23327c;
    --swoosh-grey:#c3c7d0;
    --page-white:#ffffff;
    --ink:#222222;
    --backdrop:#e9ebef;
    --sky:#6f7d8c;
    --hill-green:#7fa43a;
    --turf:#5e8f3a;
    --chestnut:#a4552a;
  }
  *{margin:0;padding:0;box-sizing:border-box}
  html,body{width:1200px;height:900px;overflow:hidden;background:var(--backdrop)}
  .spread{position:relative;width:1200px;height:900px}
  .page{position:absolute;top:78px;height:745px;background:var(--page-white);overflow:hidden}
  .page--back{left:25px;width:575px;box-shadow:0 0 0 1px #d4d6db}
  .page--front{left:600px;width:577px;box-shadow:0 0 0 1px #d4d6db}
  .page svg.page-art{position:absolute;left:0;top:0}

  .notes-heading{position:absolute;top:275px;left:0;width:100%;text-align:center;
    font-family:"Arimo",Arial,sans-serif;font-size:17px;color:var(--ink)}

  .brand-line{position:absolute;display:flex;align-items:center;gap:10px;
    font-family:"Crimson Text",Georgia,serif;color:var(--navy);line-height:1}
  .brand-mark{width:22px;height:22px;border-radius:50%;background:var(--navy);flex:none}
  .back-brand{left:44px;top:632px;font-size:21px}

  .back-address{position:absolute;left:42px;top:669px;
    font-family:"Arimo",Arial,sans-serif;font-size:10.5px;line-height:12.5px;color:var(--ink)}
  .back-contact{position:absolute;left:374px;top:645px;
    font-family:"Arimo",Arial,sans-serif;font-size:10.5px;line-height:12.5px;color:var(--ink)}
  .back-contact .web{padding-left:12px}

  .cover-ribbon{position:absolute;left:270px;top:50px;width:307px;height:77px}
  .cover-brand{position:absolute;left:308px;top:65px;display:flex;align-items:center;gap:14px;
    font-family:"Crimson Text",Georgia,serif;color:var(--navy);font-size:20px;line-height:25px}
  .cover-brand .brand-mark{width:28px;height:28px}

  .cover-date{position:absolute;left:0;width:577px;top:603px;text-align:center;
    font-family:"Arvo",Georgia,serif;font-weight:700;font-size:17px;color:#fff;padding-left:20px}
  .cover-title{position:absolute;left:0;width:577px;top:630px;text-align:center;
    font-family:"Arvo",Georgia,serif;font-weight:700;font-size:52px;color:#fff;padding-left:20px;letter-spacing:.5px}
</style>
</head>
<body>
<main class="spread">

  <section class="page page--back" aria-label="Back cover">
    <svg class="page-art" width="575" height="745" viewBox="0 0 575 745">
      <defs>
        <linearGradient id="downs-photo" x1="0" y1="0" x2="0" y2="1">
          <stop offset="0" stop-color="var(--sky)"/>
          <stop offset="0.3" stop-color="#9aa6ae"/>
          <stop offset="0.45" stop-color="#6e8a45"/>
          <stop offset="1" stop-color="var(--hill-green)"/>
        </linearGradient>
      </defs>
      <path class="swoosh-grey" d="M0,0H575V211Q300,304 0,191Z" fill="var(--swoosh-grey)"/>
      <path class="swoosh-gap" d="M0,0H575V195Q300,288 0,175Z" fill="var(--page-white)"/>
      <path class="photo-area" role="img" aria-label="Photograph of rolling chalk downland with a wooden trail signpost under a stormy sky"
            d="M0,0H575V187Q300,280 0,167Z" fill="url(#downs-photo)"/>
    </svg>

    <h2 class="notes-heading">Notes</h2>

    <div class="brand-line back-brand"><span class="brand-mark"></span>Chalkdown Racing Ltd</div>
    <address class="back-address" style="font-style:normal">
      Lower Bramcote Farm, Hollins Lane, Ashcombe<br>
      Eastbury, Berkshire, RG17 4XT
    </address>
    <address class="back-contact" style="font-style:normal">
      Phone: 01632 960418<br>
      Mobile: 07700 900582<br>
      E-mail: rhys@rhys-dalby.co.uk<br>
      <span class="web">www.rhys-dalby.co.uk</span>
    </address>
  </section>

  <section class="page page--front" aria-label="Front cover">
    <svg class="page-art" width="577" height="745" viewBox="0 0 577 745">
      <defs>
        <linearGradient id="band-navy" x1="0" y1="0" x2="0" y2="1">
          <stop offset="0" stop-color="var(--navy-deep)"/>
          <stop offset="1" stop-color="var(--navy-band-end)"/>
        </linearGradient>
        <linearGradient id="race-photo" x1="0" y1="0" x2="1" y2="1">
          <stop offset="0" stop-color="#4f8a45"/>
          <stop offset="0.35" stop-color="#c9ccc8"/>
          <stop offset="0.55" stop-color="var(--chestnut)"/>
          <stop offset="1" stop-color="var(--turf)"/>
        </linearGradient>
      </defs>
      <rect class="cover-band" width="577" height="745" fill="url(#band-navy)"/>
      <path class="swoosh-grey" d="M0,0H577V532Q250,639 0,517Z" fill="var(--swoosh-grey)"/>
      <path class="swoosh-gap" d="M0,0H577V520Q250,627 0,505Z" fill="var(--page-white)"/>
      <path class="photo-area" role="img" aria-label="Photograph of a chestnut racehorse galloping with a jockey in green and red silks, a big screen showing the race behind"
            d="M0,0H577V512Q250,619 0,497Z" fill="url(#race-photo)"/>
    </svg>

    <svg class="cover-ribbon" viewBox="0 0 307 77" aria-hidden="true">
      <polygon points="0,0 307,0 307,77 0,77 14,38" fill="var(--page-white)"/>
    </svg>
    <div class="cover-brand">
      <span class="brand-mark"></span>
      <span>Rhys Dalby<br>Chalkdown Racing Ltd</span>
    </div>

    <p class="cover-date">Sunday 11th September 2016</p>
    <h1 class="cover-title">Annual Open day</h1>
  </section>

</main>
</body>
</html>
```